Defense Attorney Business Card Design Project/ Stationary

I am looking for a distinctive business card design for my solo law practice.
I practice criminal defense, both juvenile and adult, including DUI. I am a very experienced attorney with prior military experience. The design should convey a traditional, old school flair, but not be too stodgy or uptight. Some color. My logo should appear.
Updates

Project Deadline Extended Reason: I misunderstood how this project works and I was not prepared with my logo when this project ran the first time. Added Thursday, November 13, 2014

Project Deadline Extended
Reason: I was sent overseas on military duty last year, which interrupted this project. Thank you for your participation... I hope we can get this done this week! Thank you, Neil

Target Market(s)

Regular everyday people looking for strong, knowledgeable, authoritative representation while they are faced with criminal charges. Many have never been charged with a crime before. A reassuring air is therefore desired.

Industry/Entity Type

Business

Contact Information for Business Card

My information is:
Theodore M. Quill, Attorney at Law
785 Birch Avenue Suite 300
Oakland, California 94719
Tel: (510) 384-6125
Fax: (510) 391-7802
email: neilquilllaw@mailvine.example
web: www.neilquilllaw.example

Font styles to use
Serif
Sans Serif
Decorative

Colors
0255a3
ffffff

Requirements
Must have
• Sharp lines, bold elements. Conservative use of colors, such as deep blues, burgundy, grays for example.
• While my logo says "Theodore M. Quill", it should be modified to show "Theodore M. Quill".
Should not have
• Cliche imagery such as scales of justice, gavels, Statue of Liberty, etc.

```html
<!DOCTYPE html>
<html lang="en">
<head>
<meta charset="utf-8">
<title>Theodore M. Quill — Attorney at Law — Business Card</title>
<link rel="stylesheet" href="https://fonts.googleapis.com/css2?family=Exo+2:wght@400;600&display=swap">
<style>
  :root {
    --navy: #0d3d5c;
    --paper: #ffffff;
    --frame: #d2d3d5;
    --slate: #a7a9ac;
    --backdrop: #ebe8e3;
    --ink-light: #ffffff;
  }
  * { box-sizing: border-box; margin: 0; padding: 0; }
  html, body {
    width: 1200px; height: 675px; overflow: hidden;
    background: var(--backdrop);
  }
  .card {
    position: absolute;
    left: 430px; top: 40px;
    width: 340px; height: 595px;
    background: var(--frame);
    padding: 11px;
    box-shadow: 0 6px 18px rgba(0,0,0,0.18);
  }
  .card-inner {
    width: 100%; height: 100%;
    background: var(--paper);
    display: flex; flex-direction: column;
  }
  .identity {
    height: 232px;
    display: flex; flex-direction: column;
    align-items: center; justify-content: flex-end;
    padding-bottom: 26px;
    gap: 8px;
  }
  .firm-name {
    display: flex; align-items: center; gap: 10px;
    font-family: "Exo 2", sans-serif;
    font-weight: 600;
    font-size: 26px;
    color: var(--navy);
    line-height: 1;
  }
  .firm-mark {
    width: 14px; height: 14px;
    background: var(--navy);
    flex-shrink: 0;
  }
  .firm-title {
    font-family: "Exo 2", sans-serif;
    font-weight: 400;
    font-size: 13px;
    color: var(--navy);
  }
  .contact-band {
    flex: 1;
    background: var(--navy);
    padding: 26px 28px 0;
    display: flex; flex-direction: column; gap: 14px;
  }
  .contact-row {
    display: flex; align-items: center; gap: 12px;
    font-family: "Exo 2", sans-serif;
    font-size: 13px;
    color: var(--ink-light);
    letter-spacing: 0.3px;
  }
  .contact-icon {
    width: 22px; height: 22px;
    background: var(--paper);
    border-radius: 4px;
    display: flex; align-items: center; justify-content: center;
    flex-shrink: 0;
  }
  .contact-icon svg { width: 14px; height: 14px; }
  .address-band {
    height: 88px;
    background: var(--slate);
    display: flex; align-items: center; gap: 12px;
    padding: 0 28px;
    font-family: "Exo 2", sans-serif;
    font-size: 13px;
    color: var(--ink-light);
    line-height: 1.35;
  }
  .address-band .contact-icon { background: transparent; border: 1.5px solid var(--ink-light); border-radius: 50%; }
  .address-text { font-style: normal; }
</style>
</head>
<body>
  <article class="card">
    <div class="card-inner">
      <header class="identity">
        <div class="firm-name"><span class="firm-mark"></span>Theodore M. Quill</div>
        <div class="firm-title">Attorney at Law</div>
      </header>

      <section class="contact-band">
        <div class="contact-row">
          <span class="contact-icon">
            <svg viewBox="0 0 24 24"><path fill="#0d3d5c" d="M6.6 10.8a15 15 0 0 0 6.6 6.6l2.2-2.2c.3-.3.7-.4 1-.2 1.1.4 2.3.6 3.6.6.6 0 1 .4 1 1V20c0 .6-.4 1-1 1A17 17 0 0 1 3 4c0-.6.4-1 1-1h3.5c.6 0 1 .4 1 1 0 1.3.2 2.5.6 3.6.1.3 0 .7-.2 1z"/></svg>
          </span>
          <span>(510) 384-6125</span>
        </div>
        <div class="contact-row">
          <span class="contact-icon">
            <svg viewBox="0 0 24 24"><path fill="#0d3d5c" d="M7 3h10v5H7zM4 9h16a1 1 0 0 1 1 1v7h-4v4H7v-4H3v-7a1 1 0 0 1 1-1zm5 6v4h6v-4z"/></svg>
          </span>
          <span>(510) 391-7802</span>
        </div>
        <div class="contact-row">
          <span class="contact-icon">
            <svg viewBox="0 0 24 24"><path fill="#0d3d5c" d="M3 5h18v14H3zm2 2v.5l7 5 7-5V7z"/></svg>
          </span>
          <span>neilquilllaw@mailvine.example</span>
        </div>
        <div class="contact-row">
          <span class="contact-icon">
            <svg viewBox="0 0 24 24" fill="none" stroke="#0d3d5c" stroke-width="2"><circle cx="12" cy="12" r="9"/><path d="M3 12h18M12 3c3 3 3 15 0 18M12 3c-3 3-3 15 0 18"/></svg>
          </span>
          <span>www.neilquilllaw.example</span>
        </div>
      </section>

      <footer class="address-band">
        <span class="contact-icon">
          <svg viewBox="0 0 24 24"><path fill="#ffffff" d="M12 2a7 7 0 0 0-7 7c0 5 7 13 7 13s7-8 7-13a7 7 0 0 0-7-7zm0 9.5A2.5 2.5 0 1 1 12 6.5a2.5 2.5 0 0 1 0 5z"/></svg>
        </span>
        <address class="address-text">785 Birch Avenue Suite 300 Oakland<br>California 94719</address>
      </footer>
    </div>
  </article>
</body>
</html>
```